Business card for my new company (Accounting firm)

I need a business card for my new business Brightwell Advisory and Ledger SA. Our services are accounting, tax, audit and financial management. Our customers are small companies, start-ups and new companies. The final design has to show financial security, trust and growth. Please find our logo attached to the business card. Text for the business card: Brightwell Advisory and Ledger SA Tomas Varenholt Director and Founder Certified Accountant Tel. 022 418 57 34 tv@clairevalconseil.ch www.clairevalconseil.ch Rue des Vergières 27 1201 Geneva
Target Market(s)
Our customers are small companies, start-ups and new companies.
Industry/Entity Type
Finance And Accounting
Contact Information for Business Card
Claireval Conseil et Comptes SA
Tomas Varenholt
Directeur et Fondateur
Expert-comptable diplômé
Tél. 022 418 57 34
tv@clairevalconseil.ch
www.clairevalconseil.ch
Rue des Vergières 27
1201 Genève

```html
<!DOCTYPE html>
<html lang="fr">
<head>
<meta charset="utf-8">
<title>Claireval Conseil et Comptes SA — Carte de visite</title>
<link href="https://fonts.googleapis.com/css2?family=Roboto:wght@400;500;700&display=swap" rel="stylesheet">
<style>
  :root {
    --page: #e4e5e7;
    --blue-light: #2fa3da;
    --blue-deep: #1c74b0;
    --navy: #1d5f93;
    --ink: #3a3d42;
    --paper: #f6f7f8;
    --white: #ffffff;
  }
  * { margin: 0; padding: 0; box-sizing: border-box; }
  html, body {
    width: 1200px; height: 726px; overflow: hidden;
    background: var(--page);
    font-family: "Roboto", Arial, sans-serif;
  }
  .sheet {
    position: relative; width: 1200px; height: 726px;
    display: flex; align-items: center; justify-content: center; gap: 40px;
  }
  .card {
    position: relative; width: 520px; height: 316px;
    border-radius: 4px; overflow: hidden;
    box-shadow: 0 6px 18px rgba(0,0,0,.12);
  }
  /* Front */
  .card--front {
    background: linear-gradient(160deg, var(--blue-light) 0%, var(--blue-deep) 100%);
    color: var(--white);
    display: flex; flex-direction: column; align-items: center; justify-content: center;
  }
  .brand {
    display: flex; align-items: center; gap: 12px;
  }
  .brand__mark { width: 22px; height: 22px; background: currentColor; }
  .brand__name {
    font-weight: 700; font-size: 22px; letter-spacing: .5px; line-height: 1.25;
  }
  .front__web {
    margin-top: 40px; font-size: 14px; font-weight: 500; letter-spacing: .3px;
  }
  /* Back */
  .card--back { background: var(--paper); color: var(--ink); }
  .card--back .brand {
    position: absolute; top: 44px; right: 34px; color: var(--navy);
  }
  .card--back .brand__name { font-size: 17px; text-align: right; }
  .card--back .brand__mark { width: 16px; height: 16px; }
  .divider { position: absolute; left: 0; top: 0; width: 520px; height: 316px; }
  .address {
    position: absolute; top: 128px; right: 34px; text-align: right;
    font-size: 12.5px; line-height: 1.45; font-style: normal;
  }
  .person { position: absolute; left: 34px; top: 170px; }
  .person__name { font-size: 19px; font-weight: 700; color: var(--navy); }
  .person__role { font-size: 11.5px; line-height: 1.4; margin-top: 4px; }
  .contacts { position: absolute; left: 34px; top: 234px; list-style: none; }
  .contacts li {
    display: flex; align-items: center; gap: 12px;
    font-size: 13px; line-height: 1.55;
  }
  .contacts svg { width: 12px; height: 12px; fill: var(--navy); flex: none; }
</style>
</head>
<body>
<main class="sheet">
  <section class="card card--front" aria-label="Recto">
    <div class="brand">
      <span class="brand__mark"></span>
      <span class="brand__name">Claireval Conseil<br>et Comptes SA</span>
    </div>
    <p class="front__web">www.clairevalconseil.ch</p>
  </section>

  <section class="card card--back" aria-label="Verso">
    <div class="brand">
      <span class="brand__mark"></span>
      <span class="brand__name">Claireval Conseil<br>et Comptes SA</span>
    </div>
    <svg class="divider" viewBox="0 0 520 316" aria-hidden="true">
      <path d="M190 182 C 260 176, 290 152, 340 130 S 440 112, 486 112"
            fill="none" stroke="var(--navy)" stroke-width="1.2"/>
    </svg>
    <address class="address">Rue des Vergières 27<br>1201 Genève</address>
    <div class="person">
      <h1 class="person__name">Tomas Varenholt</h1>
      <p class="person__role">Directeur et Fondateur<br>Expert-comptable diplômé</p>
    </div>
    <ul class="contacts">
      <li><svg viewBox="0 0 16 16"><path d="M3 1h3l1.5 4-2 1.3a9 9 0 0 0 4.2 4.2L11 8.5 15 10v3a2 2 0 0 1-2 2A12 12 0 0 1 1 3a2 2 0 0 1 2-2z"/></svg>022 418 57 34</li>
      <li><svg viewBox="0 0 16 16"><path d="M1 3h14v10H1z M1 3l7 6 7-6" stroke="var(--paper)" stroke-width="1.2"/></svg>tv@clairevalconseil.ch</li>
      <li><svg viewBox="0 0 16 16"><circle cx="8" cy="8" r="7"/><path d="M1 8h14M8 1c-3 3-3 11 0 14M8 1c3 3 3 11 0 14" stroke="var(--paper)" stroke-width="1" fill="none"/></svg>www.clairevalconseil.ch</li>
    </ul>
  </section>
</main>
</body>
</html>
```